Business Cards Needed for Innovative Healthcare Marketing Company

We are a marketing company focused on healthcare. Our company is all about rebranding yourself renewing your image and generating results. The phoenix stands for "reborn" or "rising" which we provide new brands for our clients we take their old brands and renew it with creativity and innovation. I am looking for a business card with color dimension. I have attached an example of a card I think has the look and feel of what I am trying to accomplish. I like that the card example has black and grey font colors, I like the font placement and the small logo, I really like the use of the colors on the right those are the colors of my logo. My logo is phoenix so maybe incorporating flames similar to that design. I would like the back a solid color maybe red with an opaque version of the logo and website. As a marketing company I am always open to creative liberty!

Target Market(s)

Doctors and business professionals.

Industry/Entity Type

Marketing

Contact Information for Business Card

Valcorne Health Care Marketing
Marla Tenwick- CEO
#(512)638-2974
email-marla@valcorne.com
website- valcorne.com

Font styles to use
Sans Serif

Colors
ec1f27
f37122
ffc214
fbed22
fbf289
f04a50

Requirements
Must have
• The logo and required information
Nice to have
• icons by the information
Should not have
• child like font

```html
<!DOCTYPE html>
<html lang="en">
<head>
<meta charset="utf-8">
<title>Valcorne Health Care Marketing – Business Card</title>
<link href="https://fonts.googleapis.com/css2?family=Varela+Round&display=swap" rel="stylesheet">
<style>
  :root {
    --backdrop: #ece7df;
    --paper: #ffffff;
    --ink: #1c1c1c;
    --brand-red: #a01f22;
    --accent-red: #b3262a;
    --flame-orange: #f0962a;
    --ember: #b8402e;
    --deep-ember: #a3322d;
    --rust: #c0392b;
    --faint-mark: rgba(255, 140, 140, 0.35);
  }
  * { box-sizing: border-box; margin: 0; padding: 0; }
  html, body {
    width: 1181px; height: 1200px; overflow: hidden;
    background: var(--backdrop);
    font-family: "Varela Round", sans-serif;
  }
  .stage { position: relative; width: 1181px; height: 1200px; }

  .card { position: absolute; overflow: hidden; box-shadow: 2px 3px 6px rgba(0,0,0,.25); }
  .card--front { left: 201px; top: 95px; width: 790px; height: 461px; background: var(--paper); }
  .card--back  { left: 193px; top: 637px; width: 807px; height: 472px; background: var(--brand-red); }

  .front-flames { position: absolute; inset: 0; }

  .brand { position: absolute; left: 47px; top: 40px; display: flex; align-items: center; gap: 14px; }
  .brand__dot { width: 56px; height: 56px; border-radius: 50%; background: var(--flame-orange); }
  .brand__name { color: var(--accent-red); font-size: 17px; line-height: 1.2; width: 130px; }

  .person { position: absolute; left: 49px; top: 244px; }
  .person__name { font-size: 28px; color: var(--ink); line-height: 1.1; }
  .person__role { font-size: 20px; color: var(--accent-red); margin-top: 2px; }

  .contacts { position: absolute; left: 51px; top: 322px; list-style: none; }
  .contacts li { display: flex; align-items: center; height: 34px; font-size: 18px; color: var(--ink); }
  .contacts svg { width: 20px; height: 20px; margin-right: 13px; fill: var(--accent-red); }

  .back-brand { position: absolute; left: 153px; top: 160px; display: flex; align-items: center; gap: 26px; }
  .back-brand__dot { width: 120px; height: 120px; border-radius: 50%; background: var(--faint-mark); }
  .back-brand__name { color: var(--faint-mark); font-size: 48px; line-height: 1.15; letter-spacing: 2px; width: 380px; }
</style>
</head>
<body>
<main class="stage">
  <section class="card card--front" aria-label="Card front">
    <svg class="front-flames" viewBox="0 0 790 461" aria-hidden="true">
      <ellipse cx="700" cy="410" rx="272" ry="235" fill="var(--flame-orange)"/>
      <ellipse cx="640" cy="115" rx="304" ry="162" fill="var(--ember)" opacity=".95"/>
      <ellipse cx="700" cy="70" rx="305" ry="150" fill="var(--deep-ember)" opacity=".9"/>
      <ellipse cx="790" cy="300" rx="278" ry="260" fill="var(--rust)" opacity=".5"/>
    </svg>

    <div class="brand">
      <span class="brand__dot"></span>
      <span class="brand__name">Valcorne Health Care Marketing</span>
    </div>

    <div class="person">
      <p class="person__name">Marla Tenwick</p>
      <p class="person__role">CEO</p>
    </div>

    <ul class="contacts">
      <li>
        <svg viewBox="0 0 20 20" aria-hidden="true"><path d="M2 7c0-3 4-4 8-4s8 1 8 4v2h-4V7H6v2H2z"/><path d="M5 10h10l2 7H3z"/></svg>
        (512)638-2974
      </li>
      <li>
        <svg viewBox="0 0 20 20" aria-hidden="true"><path d="M1 4h18v12H1z"/><path d="M1 4l9 7 9-7" fill="none" stroke="#fff" stroke-width="1.6"/></svg>
        email-marla@valcorne.com
      </li>
      <li>
        <svg viewBox="0 0 20 20" aria-hidden="true" style="fill:none;stroke:var(--accent-red);stroke-width:1.4"><circle cx="10" cy="10" r="8"/><ellipse cx="10" cy="10" rx="3.5" ry="8"/><path d="M2 10h16M3.5 6h13M3.5 14h13"/></svg>
        website- valcorne.com
      </li>
    </ul>
  </section>

  <section class="card card--back" aria-label="Card back">
    <div class="back-brand">
      <span class="back-brand__dot"></span>
      <span class="back-brand__name">Valcorne Health Care Marketing</span>
    </div>
  </section>
</main>
</body>
</html>
```